Finding the Root: Reason in Clinical Choice-Crafting

I'd like a cover that looks like it would fit on the shelf next to "The Illness Mirage" by Corwin Talley, "The Close of Forgetting" by Hugh Marchetti, "Meal Mend" by Paul Grieve, "The Energy Restart Plan" by Oscar Pemberley or "The Gland Restart Plan" by the same or "The Cortex Restart Plan" by the same ... either text only (with some interesting fonts that make the title stand out, and the subtitle smaller) or a relevant image, though I'm not entirely sure what that would be since this is a book about big-picture medical decision making.
Author name is Dr Tessa Morrow, NMD
I'll eventually request an e-book, paperback, and audio cover from the winner...

Target Market(s)

practicing physicians

Industry/Entity Type

medicine

Requirements
Must have
• look similar to other books in the genre

```html
<!DOCTYPE html>
<html lang="en">
<head>
<meta charset="utf-8">
<title>Finding the Root — Book Cover</title>
<link rel="stylesheet" href="https://fonts.googleapis.com/css2?family=Playfair+Display:wght@900&family=Tinos:wght@400;700&display=swap">
<style>
  :root {
    --stage: #cfcfcf;
    --paper: #ffffff;
    --paper-shade: #e4e4e4;
    --ink-dark: #333333;
    --navy: #002c4f;
    --teal: #0e5b79;
    --teal-light: #19809c;
    --green-ink: #1c4a4a;
    --rule: #333333;
    --white: #ffffff;
  }
  html, body {
    margin: 0;
    padding: 0;
    width: 1200px;
    height: 2615px;
    overflow: hidden;
    background: var(--stage);
  }
  .cover {
    position: absolute;
    left: 100px;
    top: 557px;
    width: 1000px;
    height: 1500px;
    overflow: hidden;
    background: radial-gradient(ellipse 75% 55% at 50% 48%, var(--paper) 60%, var(--paper-shade) 100%);
    box-shadow: 14px 18px 30px rgba(0,0,0,0.25);
  }
  .cover__band {
    position: absolute;
    left: 0;
    top: 979px;
    width: 100%;
    height: 521px;
    background: radial-gradient(ellipse 60% 70% at 50% 45%, var(--teal-light) 0%, var(--teal) 70%, #0b4d68 100%);
  }
  .cover__kicker {
    position: absolute;
    top: 118px;
    width: 100%;
    text-align: center;
    font-family: "Tinos", "Times New Roman", serif;
    font-size: 100px;
    line-height: 1;
    letter-spacing: 2px;
    color: var(--ink-dark);
  }
  .cover__title {
    position: absolute;
    top: 190px;
    width: 100%;
    text-align: center;
    font-family: "Playfair Display", "Bodoni Moda", serif;
    font-weight: 900;
    font-size: 270px;
    line-height: 1;
    letter-spacing: -4px;
    background: linear-gradient(100deg, var(--navy) 35%, #156d8a 80%, var(--navy) 100%);
    -webkit-background-clip: text;
    background-clip: text;
    color: transparent;
  }
  .cover__subtitle {
    position: absolute;
    top: 518px;
    width: 100%;
    text-align: center;
    font-family: "Tinos", "Times New Roman", serif;
    color: var(--ink-dark);
  }
  .subtitle__line {
    display: flex;
    align-items: center;
    justify-content: center;
    gap: 18px;
    font-size: 54px;
    line-height: 56px;
  }
  .subtitle__line--ruled::before,
  .subtitle__line--ruled::after {
    content: "";
    width: 165px;
    height: 2px;
    background: var(--rule);
  }
  .subtitle__accent {
    font-weight: 700;
    font-size: 52px;
    line-height: 64px;
    color: var(--green-ink);
  }
  .cover__emblem {
    position: absolute;
    left: 253px;
    top: 742px;
    width: 494px;
    height: 494px;
  }
  .cover__author {
    position: absolute;
    top: 1312px;
    width: 100%;
    text-align: center;
    font-family: "Tinos", "Times New Roman", serif;
    font-size: 48px;
    color: var(--white);
  }
</style>
</head>
<body>
  <main class="cover">
    <div class="cover__band"></div>

    <h1 class="cover__heading">
      <span class="cover__kicker">FINDING THE</span>
      <span class="cover__title">ROOT</span>
    </h1>

    <div class="cover__subtitle">
      <div class="subtitle__line subtitle__line--ruled">Reason in</div>
      <div class="subtitle__line">Clinical</div>
      <div class="subtitle__line subtitle__accent">Choice-Crafting</div>
    </div>

    <svg class="cover__emblem" viewBox="0 0 494 494" role="img" aria-label="Circular maze illustration with a golden path leading to a light bulb at its centre">
      <defs>
        <radialGradient id="maze-tone" cx="50%" cy="50%" r="50%">
          <stop offset="0%" stop-color="#0d4f6c"/>
          <stop offset="55%" stop-color="#2a8aa6"/>
          <stop offset="100%" stop-color="#9fd0de"/>
        </radialGradient>
      </defs>
      <circle cx="247" cy="247" r="247" fill="#ffffff"/>
      <circle cx="247" cy="247" r="228" fill="url(#maze-tone)"/>
    </svg>

    <p class="cover__author">Dr Tessa Morrow, NMD</p>
  </main>
</body>
</html>
```